KRV Cartridge chip board folding ammuniton boxes for retail sale

Design a scalable design for use with 20 round and 50 round boxes for Ammunition. The caliber will be 9mm but will need to be editable, all warnings and barcodes will need to be able to be edited also. I have attached the company logo.

**UPDATE**
Box dimensions
20rd= 2.55in long X 2.1in width X 1.25in height

50rd= 5.1in long x 2.6in width X 1.2in height

Please see the bullet picture i would like used if possible.

Target Market(s)

Quality shooting sports, self defense

Industry/Entity Type

Self Defense

Requirements
Must have
• supplied company logo design
Should not have
• any cartoons of any kind

```html
<!DOCTYPE html>
<html lang="en">
<head>
<meta charset="utf-8">
<title>KRV Cartridge – 9mm FMJ 50 Round Box</title>
<link rel="stylesheet" href="https://fonts.googleapis.com/css2?family=Saira+Condensed:wght@400;500;600&family=Saira:wght@700&display=swap">
<style>
  :root {
    --backdrop: #d3e1e8;
    --camo-dark: #2f3b38;
    --camo-mid: #56625c;
    --camo-light: #8b968d;
    --band-red: #d81f2a;
    --band-red-deep: #b3141e;
    --panel-black: #121717;
    --panel-smoke: #2a3230;
    --ink-white: #f4f4f2;
    --ink-grey: #9aa3a0;
    --brass-light: #e7c274;
    --brass-dark: #9a6a2c;
  }
  html, body {
    margin: 0;
    width: 1200px;
    height: 840px;
    overflow: hidden;
    background: var(--backdrop);
  }
  .box-net {
    display: block;
    width: 1200px;
    height: 840px;
  }
  .band-label {
    font-family: "Saira Condensed", sans-serif;
    font-weight: 600;
    fill: var(--ink-white);
  }
  .caliber-mark {
    font-family: "Saira Condensed", sans-serif;
    font-weight: 600;
  }
  .caliber-mark--type { fill: var(--band-red); }
  .caliber-mark--size { fill: var(--ink-white); }
  .brand-name {
    font-family: "Saira", sans-serif;
    font-weight: 700;
    fill: var(--ink-white);
  }
  .brand-dot { fill: var(--band-red); }
  .warning-copy {
    font-family: "Saira Condensed", sans-serif;
    font-weight: 400;
    font-size: 14px;
    fill: var(--ink-grey);
  }
</style>
</head>
<body>
<svg class="box-net" viewBox="0 0 1200 840" xmlns="http://www.w3.org/2000/svg">
  <defs>
    <linearGradient id="camoTone" x1="0" y1="0" x2="1" y2="1">
      <stop offset="0" stop-color="var(--camo-mid)"/>
      <stop offset="0.5" stop-color="var(--camo-dark)"/>
      <stop offset="1" stop-color="var(--camo-light)"/>
    </linearGradient>
    <linearGradient id="sideTone" x1="0" y1="0" x2="1" y2="1">
      <stop offset="0" stop-color="var(--panel-smoke)"/>
      <stop offset="1" stop-color="var(--panel-black)"/>
    </linearGradient>
    <linearGradient id="redBand" x1="0" y1="1" x2="1" y2="0">
      <stop offset="0" stop-color="var(--band-red-deep)"/>
      <stop offset="1" stop-color="var(--band-red)"/>
    </linearGradient>
    <linearGradient id="brassTone" x1="0" y1="0" x2="1" y2="1">
      <stop offset="0" stop-color="var(--brass-light)"/>
      <stop offset="1" stop-color="var(--brass-dark)"/>
    </linearGradient>
    <clipPath id="lidClip"><rect x="270" y="165" width="870" height="510"/></clipPath>
  </defs>

  <!-- End panel: lead warning -->
  <g class="end-panel">
    <rect class="end-panel-face" x="60" y="165" width="200" height="510" fill="url(#sideTone)"/>
    <text class="warning-copy" transform="translate(228 195) rotate(90)">
      <tspan x="0" dy="0">LEAD WARNING: Discharging firearms in poorly ventilated areas,</tspan>
      <tspan x="0" dy="22">cleaning firearms, or handling ammunition may result in exposure</tspan>
      <tspan x="0" dy="22">to lead and other substances known to cause birth defects,</tspan>
      <tspan x="0" dy="22">reproductive harm, and other serious physical injury. Have adequate</tspan>
      <tspan x="0" dy="22">ventilation at all times. Wash hands thoroughly after exposure.</tspan>
    </text>
  </g>

  <!-- Lid face -->
  <g class="lid-face" clip-path="url(#lidClip)">
    <rect class="camo-field" x="270" y="165" width="870" height="510" fill="url(#camoTone)"
          role="img" aria-label="Woodland camouflage pattern in grey-green tones"/>
    <polygon class="base-black" points="270,675 270,665 1140,375 1140,675" fill="var(--panel-black)"/>
    <polygon class="red-band" points="270,575 1140,270 1140,375 270,665" fill="url(#redBand)"/>
  </g>

  <g class="brand-lockup" transform="translate(320 470) rotate(-19)">
    <text class="brand-name" x="0" y="0" font-size="64">KRV Cartridge</text>
    <circle class="brand-dot" cx="492" cy="-22" r="22"/>
  </g>

  <rect class="cartridge-photo" x="640" y="375" width="220" height="130" rx="18"
        transform="rotate(-19 750 440)" fill="url(#brassTone)"
        role="img" aria-label="Photo of several 9mm full metal jacket cartridges with brass cases"/>

  <rect class="single-cartridge-photo" x="918" y="485" width="38" height="115" rx="10"
        fill="url(#brassTone)" role="img" aria-label="Photo of a single 9mm cartridge standing upright"/>

  <text class="band-label" x="290" y="645" font-size="50" transform="rotate(-19 290 645)">50 ROUND</text>
  <text class="band-label" x="895" y="420" font-size="42" transform="rotate(-19 895 420)">9mm FMJ</text>

  <text class="caliber-mark caliber-mark--type" x="975" y="505" font-size="46" transform="rotate(-19 975 505)">FMG</text>
  <text class="caliber-mark caliber-mark--size" x="968" y="590" font-size="76" transform="rotate(-19 968 590)">9mm</text>
</svg>
</body>
</html>
```